Signage Design Project

Busisness is a bakery and deli long time owned by the Tavel family. Want to develop a new outside sign that communicates it is a deli and a bakery but keeps the tavel name in the design.

The sign when produced will be about 10' by 3' . It is not lighted at present but could be if it were advantageous.

The name of the store is:

Tavel's Harbor Lane Bakery and Deli. The concept is to have a new,modern sign that reinforces that it is a deli and a bakery, as most people only know about the bakery side of the business
Updates

The name Tavel is just a reinforcer so the people kno it is still in the family.  The emphasis should be on the HARBOR LANE BAKERY and DELI

Target Market(s)

Small business breakfast and lunch customers

Industry/Entity Type

Bakery

Requirements
Must have
• Great impact from the road. Communicate that it is a deli and a bakery. Keep the Tavel name but need not be a major design element

```html
<!DOCTYPE html>
<html lang="en">
<head>
<meta charset="utf-8">
<title>Tavel's Harbor Lane Bakery and Deli – Sign</title>
<link rel="stylesheet" href="https://fonts.googleapis.com/css2?family=Fondamento:ital@1&family=Titan+One&display=swap">
<style>
  :root {
    --wine-centre: #8e1c4c;
    --wine-mid: #6e1239;
    --wine-edge: #4a0622;
    --gold: #f1c419;
    --gold-light: #fbe36a;
    --gold-deep: #c98f08;
    --shadow: #3a0418;
    --flourish: rgba(214, 150, 180, 0.28);
  }
  html, body {
    margin: 0;
    padding: 0;
    overflow: hidden;
    background: #ffffff;
  }
  .sign {
    position: relative;
    width: 1200px;
    height: 360px;
    overflow: hidden;
    background: radial-gradient(ellipse 60% 85% at 50% 45%, var(--wine-centre) 0%, var(--wine-mid) 60%, var(--wine-edge) 100%);
  }
  .flourish {
    position: absolute;
    top: 14px;
    width: 64px;
    height: 332px;
  }
  .flourish--left { left: 16px; }
  .flourish--right { right: 16px; }
  .title-line {
    position: absolute;
    left: 0;
    right: 0;
    top: 48px;
    display: flex;
    justify-content: center;
    align-items: baseline;
    gap: 22px;
    font-family: "Fondamento", "Palatino Linotype", serif;
    font-style: italic;
  }
  .family-name {
    font-size: 52px;
    color: var(--gold);
    text-shadow: 2px 2px 0 var(--shadow);
  }
  .place-name {
    font-size: 104px;
    line-height: 1.2;
    background: linear-gradient(180deg, var(--gold-light) 0%, var(--gold) 45%, var(--gold-deep) 100%);
    -webkit-background-clip: text;
    background-clip: text;
    color: transparent;
    filter: drop-shadow(4px 4px 0 var(--shadow));
  }
  .trade-line {
    position: absolute;
    left: 0;
    right: 0;
    top: 210px;
    margin: 0;
    text-align: center;
    font-family: "Titan One", "Arial Black", sans-serif;
    font-weight: 400;
    font-size: 96px;
    line-height: 1;
    letter-spacing: 2px;
    color: var(--gold);
  }
</style>
</head>
<body>
  <div class="sign">
    <svg class="flourish flourish--left" viewBox="0 0 64 332" role="img" aria-label="Vertical scroll flourish ornament">
      <rect x="0" y="0" width="64" height="332" rx="32" fill="var(--flourish)"/>
    </svg>
    <svg class="flourish flourish--right" viewBox="0 0 64 332" role="img" aria-label="Vertical scroll flourish ornament">
      <rect x="0" y="0" width="64" height="332" rx="32" fill="var(--flourish)"/>
    </svg>

    <h1 class="title-line">
      <span class="family-name">Tavel's</span>
      <span class="place-name">Harbor Lane</span>
    </h1>
    <p class="trade-line">Bakery and Deli</p>
  </div>
</body>
</html>
```